professional business card design

Business card design. Photos have been uploaded and i am open to the designer choosing which photos to use. Would like the card to be mostyly in a grey scale design with black, whites, silver & grey colours. I have added copy of our flyer as would like on the back side of card our services to be listed. Do not use any bright colurs such as blue red green or yellow. i need to be able to edit the phone number and naem in the final card design submitted.

Target Market(s)

Clients

Industry/Entity Type

earhmovibng and transport

Contact Information for Business Card

Director Name, address, email, phone number and services

Colors

Designer to choose only greyscale colors for use in the design.

Requirements
Should not have
• no yellow, red, blue or green

```html
<!DOCTYPE html>
<html lang="en">
<head>
<meta charset="utf-8">
<title>Business Card – Services and Contact</title>
<link rel="stylesheet" href="https://fonts.googleapis.com/css2?family=Archivo:ital,wght@0,400;0,500;0,700;0,800;1,400&display=swap">
<style>
  :root {
    --page-bg: #2b2b2b;
    --steel-light: #e4e4e4;
    --steel-mid: #b9b9b9;
    --steel-dark: #8e8e8e;
    --ink: #111111;
    --ink-soft: #2a2a2a;
    --photo-sky: #9fc3dc;
    --photo-ground: #8a7060;
  }
  * { box-sizing: border-box; margin: 0; padding: 0; }
  html, body { width: 1200px; height: 1015px; overflow: hidden; }
  body {
    background: var(--page-bg);
    font-family: "Archivo", Arial, sans-serif;
    color: var(--ink);
    display: flex;
    flex-direction: column;
    align-items: center;
    gap: 25px;
    padding-top: 25px;
  }
  .card {
    position: relative;
    width: 860px;
    height: 470px;
    overflow: hidden;
    background:
      radial-gradient(ellipse at 35% 45%, rgba(255,255,255,0.55), rgba(255,255,255,0) 60%),
      linear-gradient(135deg, var(--steel-mid) 0%, var(--steel-light) 40%, var(--steel-mid) 70%, var(--steel-dark) 100%);
    box-shadow: 0 10px 30px rgba(0,0,0,0.5);
  }

  /* Services side */
  .services { position: absolute; left: 48px; top: 38px; width: 440px; }
  .services-title { font-weight: 800; font-size: 23px; letter-spacing: 0.5px; margin-bottom: 6px; }
  .services-list { list-style: none; font-size: 19px; line-height: 1.22; }
  .services-list li { position: relative; padding-left: 24px; }
  .services-list li::before {
    content: ""; position: absolute; left: 2px; top: 8px;
    width: 9px; height: 9px; border-radius: 50%; background: var(--ink);
  }
  .services-note { margin-top: 12px; font-size: 19px; line-height: 1.25; width: 440px; }
  .services-note em { font-style: italic; font-weight: 400; }
  .services-note strong { font-weight: 800; }
  .photo-area {
    position: absolute; right: -150px; top: -120px;
    width: 620px; height: 620px; border-radius: 50%;
    background: linear-gradient(180deg, var(--photo-sky) 0%, #cfdde6 50%, #c9c9c9 62%, var(--photo-ground) 100%);
  }

  /* Contact side */
  .identity { position: absolute; left: 70px; top: 170px; }
  .person-name { font-weight: 800; font-size: 32px; letter-spacing: 0.5px; }
  .person-role { font-size: 19px; letter-spacing: 1px; color: var(--ink-soft); margin-top: 2px; }
  .contact-list { list-style: none; margin-top: 22px; font-size: 23px; line-height: 1.3; }
  .contact-list li { display: flex; align-items: center; gap: 10px; }
  .contact-list svg { width: 20px; height: 20px; flex: none; }
  .address { margin-top: 24px; font-size: 23px; line-height: 1.25; padding-left: 30px; }
  .brand-name {
    position: absolute; right: 56px; top: 100px;
    font-weight: 800; font-size: 50px; letter-spacing: 2px; color: var(--ink-soft);
  }
</style>
</head>
<body>

<section class="card card-services">
  <div class="photo-area" role="img" aria-label="Photo of a white road train prime mover hauling heavy earthmoving machinery under a cloudy sky"></div>
  <div class="services">
    <h2 class="services-title">OUR SERVICES</h2>
    <ul class="services-list">
      <li>Over size loads/hot shot loads</li>
      <li>Heavy vehicle recovery services</li>
      <li>Potable water deliveries</li>
      <li>Road building/maintenance</li>
      <li>Earthworks</li>
      <li>Sand &amp; metal supply &amp; cartage</li>
      <li>Road train tippers</li>
      <li>Road train tankers</li>
      <li>Road train flat tops</li>
      <li>Drop deck trailers</li>
      <li>Mine site accredited</li>
      <li>Equipment &amp; operators</li>
    </ul>
    <p class="services-note"><em>we offer a large range of services not listed</em> <strong>so call us today for a personalised quote to suit your needs.</strong></p>
  </div>
</section>

<section class="card card-contact">
  <div class="brand-name">GRANITE HAUL</div>
  <div class="identity">
    <h1 class="person-name">DANIEL REEVES</h1>
    <p class="person-role">MANAGING DIRECTOR</p>
    <ul class="contact-list">
      <li>
        <svg viewBox="0 0 24 24" aria-hidden="true"><path fill="#111" d="M6.6 10.8a15 15 0 0 0 6.6 6.6l2.2-2.2a1 1 0 0 1 1-.25 11.4 11.4 0 0 0 3.6.57 1 1 0 0 1 1 1V20a1 1 0 0 1-1 1A17 17 0 0 1 3 4a1 1 0 0 1 1-1h3.5a1 1 0 0 1 1 1c0 1.25.2 2.45.57 3.57a1 1 0 0 1-.25 1z"/></svg>
        044-987 650 312
      </li>
      <li>
        <svg viewBox="0 0 24 24" aria-hidden="true"><rect x="2" y="5" width="20" height="14" fill="#111"/><path d="M2 5l10 8 10-8" stroke="#ddd" stroke-width="1.6" fill="none"/></svg>
        info@granitehaul.com
      </li>
      <li>
        <svg viewBox="0 0 24 24" aria-hidden="true"><circle cx="12" cy="12" r="9.5" fill="none" stroke="#111" stroke-width="2"/><ellipse cx="12" cy="12" rx="4" ry="9.5" fill="none" stroke="#111" stroke-width="1.6"/><path d="M2.5 12h19M4 7h16M4 17h16" stroke="#111" stroke-width="1.4"/></svg>
        www.granitehaul.com
      </li>
    </ul>
    <p class="address">18 Quarry Road, Stonebridge<br>45921, Northland</p>
  </div>
</section>

</body>
</html>
```